International Clinical Software Company needs a new business card design

We are looking for a new business card design for our company that has recently expanded into the UK market, making us a multinational company.
After having rebranded our website and produced a new style guide, we are looking for a business card that is creative and attention grabbing, while being consistent with the style and colour scheme used on the new website, www.plumvora.example
We produce care management technology for the aged care market, but the main aspect we aim to communicate is the human element of our software, and the way it assists in providing better care for aged people, and stronger relationships between aged people and the staff that care for them.
Our current business card is a dark green with gold text, which makes the text quite difficult to read, not very aesthetically appealing and the colour scheme looks quite dated.
We would like something fresh and modern, that can still be colourful but doesn't use large blocks of dark colour, and uses the colours within our logo.
Something tying in with the leaves that are used in our logo could work quite nicely, along with the Autumn/Fall colours of soft greens, yellows and reds (also in our existing logo). However also happy to look at fresh, completely out of the box ideas we may not have yet considered.
Target Market(s)
The people that receive this business card work in the aged card or health industry and are either corporate/management level staff or clinical (Registered Nurses, care workers etc.)
Industry/Entity Type
Health Product
Contact Information for Business Card
Company Name - BrindlewayCare
Company locations: United Kingdom, Australia, New Zealand
Staff Details:
Staff name: Derek Mallow
Staff job title: Executive Chairman
Staff email: d.mallow@plumvora.example
Office phone number: 01742 918576
Font styles to use
Other font styles liked:
- Calibri
Requirements
Must have
- Must include the BrindlewayCare brand name in it's current font
- Must include logo (3 leaves in gold circle)
- Must include Business Card Details
Nice to have
- Elements of gold
- White space
- Something autumn themed but not too cliched
Should not have
- No blue - used by a major competitor and we would like to differentiate from them
- Large blocks of dark green colour (the green that appears in our leaves on the logo on our current business card is the background colour and it is far too dark)

```html
<!DOCTYPE html>
<html lang="en">
<head>
<meta charset="utf-8">
<title>BrindlewayCare – Business Card</title>
<link rel="stylesheet" href="https://fonts.googleapis.com/css2?family=Open+Sans:wght@400;600&display=swap">
<style>
  :root {
    --backdrop: #8c8c8c;
    --card: #f5f5f7;
    --gold: #9d8a60;
    --crimson: #a5173f;
    --ink: #3b3b3d;
    --rule: #b9b4aa;
    --white: #ffffff;
  }
  * { box-sizing: border-box; margin: 0; padding: 0; }
  html, body {
    width: 1105px; height: 1200px; overflow: hidden;
    background: var(--backdrop);
    font-family: "Open Sans", Calibri, sans-serif;
  }
  .business-card {
    position: absolute; left: 52px; top: 314px;
    width: 1000px; height: 571px;
    background: var(--card);
    overflow: hidden;
  }
  .brand-mark {
    position: absolute; left: 248px; top: 170px;
    width: 122px; height: 122px;
    border: 4px solid var(--gold); border-radius: 50%;
  }
  .brand-name {
    position: absolute; left: 60px; width: 430px; top: 318px;
    text-align: center;
    font-size: 44px; font-weight: 400; letter-spacing: 0.5px;
    color: var(--gold);
  }
  .divider {
    position: absolute; left: 506px; top: 155px;
    width: 1px; height: 240px; background: var(--rule);
  }
  .person { position: absolute; left: 556px; top: 163px; }
  .person-name { font-size: 33px; font-weight: 600; color: var(--gold); line-height: 44px; }
  .person-title { font-size: 27px; font-weight: 400; color: var(--crimson); line-height: 36px; }
  .contact-list { position: absolute; left: 572px; top: 275px; list-style: none; }
  .contact-item {
    display: flex; align-items: center; gap: 12px;
    height: 38px; font-size: 25px; color: var(--ink);
  }
  .contact-icon { width: 22px; height: 22px; fill: var(--gold); flex: none; }
  .accent-line {
    position: absolute; left: 0; top: 508px;
    width: 100%; height: 3px; background: var(--crimson);
  }
  .locations-band {
    position: absolute; left: 0; top: 518px;
    width: 100%; height: 53px; background: var(--gold);
    display: flex; align-items: center; justify-content: center;
    font-size: 27px; color: var(--white);
  }
</style>
</head>
<body>
  <div class="business-card">
    <div class="brand-mark"></div>
    <div class="brand-name">BrindlewayCare</div>

    <div class="divider"></div>

    <div class="person">
      <p class="person-name">Derek Mallow</p>
      <p class="person-title">Executive Chairman</p>
    </div>

    <ul class="contact-list">
      <li class="contact-item">
        <svg class="contact-icon" viewBox="0 0 24 24" aria-hidden="true"><path d="M6.6 10.8a15.2 15.2 0 0 0 6.6 6.6l2.2-2.2c.3-.3.7-.4 1-.2 1.1.4 2.3.6 3.6.6.6 0 1 .4 1 1V20c0 .6-.4 1-1 1A17 17 0 0 1 3 4c0-.6.4-1 1-1h3.5c.6 0 1 .4 1 1 0 1.3.2 2.5.6 3.6.1.3 0 .7-.2 1z"/></svg>
        <span>01742 918576</span>
      </li>
      <li class="contact-item">
        <svg class="contact-icon" viewBox="0 0 24 24" aria-hidden="true"><path d="M2 5h20v14H2z M3.5 6.5 12 13l8.5-6.5" fill="none" stroke="#9d8a60" stroke-width="0"/><path d="M2 5h20v2l-10 6L2 7z"/><path d="M2 9l10 6 10-6v10H2z"/></svg>
        <span>d.mallow@plumvora.example</span>
      </li>
      <li class="contact-item">
        <svg class="contact-icon" viewBox="0 0 24 24" aria-hidden="true"><circle cx="12" cy="12" r="10"/><path d="M7 7c2 0 3 1 3 3s-2 2-2 4 2 2 2 4M15 5c-1 2 0 3 2 4s3 2 2 5" fill="none" stroke="#f5f5f7" stroke-width="1.6"/></svg>
        <span>www.plumvora.example</span>
      </li>
    </ul>

    <div class="accent-line"></div>
    <div class="locations-band">United Kingdom | Australia | &nbsp;New Zealand</div>
  </div>
</body>
</html>
```